High-end construction company needs a business card design

We need a modern looking business card that draws people in, is memorable and looks so good people will want to sick it on their fridges.
On the first side what is needed are:
Logo
My name - Tomasz Brelwik
Title - Managing Director
Website - www.varkelt.co.uk
Email - tomasz@varkelt.co.uk
Telephone - 020 5194 6281
Mobile - 07845139072
On the back side was is needed is a list of all the services we provide:
-Kitchen Renovations
-Bathroom Renovations
-House Renovations
-Garage Conversions
-Extensions
-Loft Conversions
-Conservatories
-Carpentry
-Tiling
-Electrical
-Plumbing & Heating
-Bricklaying
-Landscaping
-Decorating
-Plastering
We would like the colours to be the same shades as on the logo with grey or black for the words.
Target Market(s)
Anyone who needs building work done
Contact Information for Business Card
This business card is for a construction company which strives to deliver excellent service and quality.
The look and feel of the card should represent this.
Requirements
Must have
- On the first side what is needed are:
Logo
My name - Tomasz Brelwik
Title - Managing Director
Website - www.varkelt.co.uk
Email - tomasz@varkelt.co.uk
Telephone - 020 5194 6281
Mobile - 07845139072
Nice to have
- Cool looking features

```html
<!DOCTYPE html>
<html lang="en">
<head>
<meta charset="utf-8">
<title>Varkelt Construction Ltd – Business Card</title>
<link rel="stylesheet" href="https://fonts.googleapis.com/css2?family=Exo+2:wght@400;600&display=swap">
<style>
  :root {
    --backdrop: #e6e6e6;
    --paper: #ffffff;
    --green-light: #76bc43;
    --green-dark: #4a8c3f;
    --text-light: #ffffff;
  }
  * { box-sizing: border-box; margin: 0; padding: 0; }
  html, body {
    width: 1125px;
    height: 1200px;
    overflow: hidden;
    background: var(--backdrop);
    font-family: "Exo 2", sans-serif;
  }
  .canvas { position: relative; width: 1125px; height: 1200px; }

  .card {
    position: absolute;
    left: 162px;
    width: 800px;
    height: 456px;
    overflow: hidden;
  }
  .card--front { top: 103px; background: var(--paper); }
  .card--back  { top: 620px; background: var(--green-dark); }

  /* Front: wordmark */
  .wordmark {
    position: absolute;
    left: 0; right: 0;
    top: 190px;
    text-align: center;
    color: var(--green-light);
    font-weight: 600;
  }
  .wordmark__name {
    display: block;
    font-size: 76px;
    line-height: 1;
    letter-spacing: 2px;
  }
  .wordmark__tagline {
    display: block;
    margin-top: 8px;
    font-size: 21px;
    letter-spacing: 3.5px;
  }

  /* Front: contact band */
  .contact-band {
    position: absolute;
    left: 0; right: 0; bottom: 0;
    height: 76px;
    display: grid;
    grid-template-columns: 269px 268px 259px;
    column-gap: 2px;
    background: var(--paper);
  }
  .contact-band__cell {
    display: flex;
    flex-direction: column;
    justify-content: center;
    color: var(--text-light);
  }
  .contact-band__cell--identity { background: var(--green-light); padding-left: 49px; }
  .contact-band__cell--phones   { background: var(--green-dark);  padding-left: 50px; }
  .contact-band__cell--online   { background: var(--green-light); padding-left: 58px; }

  .identity__name  { font-size: 26px; font-weight: 600; line-height: 1.05; }
  .identity__title { font-size: 17px; font-weight: 400; line-height: 1.2; }

  .contact-line {
    display: flex;
    align-items: center;
    gap: 12px;
    font-size: 17.5px;
    line-height: 23px;
  }
  .contact-band__cell--online .contact-line { font-size: 16.5px; gap: 9px; }
  .contact-line svg { width: 14px; height: 14px; flex: none; fill: var(--text-light); }

  /* Back */
  .back-mark {
    position: absolute;
    left: 0; right: 0;
    top: 190px;
    text-align: center;
    color: var(--text-light);
    font-weight: 600;
    font-size: 68px;
    line-height: 1;
    letter-spacing: 2px;
  }
  .back-rule {
    position: absolute;
    left: 137px;
    width: 502px;
    top: 270px;
    height: 3px;
    background: var(--text-light);
  }
  .services {
    position: absolute;
    left: 0; right: 0;
    top: 304px;
    text-align: center;
    color: var(--text-light);
    font-size: 17px;
    line-height: 22.7px;
    list-style: none;
  }
</style>
</head>
<body>
<main class="canvas">

  <section class="card card--front" aria-label="Business card front">
    <div class="wordmark">
      <span class="wordmark__name">VARKELT</span>
      <span class="wordmark__tagline">CONSTRUCTION LTD</span>
    </div>

    <div class="contact-band">
      <div class="contact-band__cell contact-band__cell--identity">
        <p class="identity__name">Tomasz Brelwik</p>
        <p class="identity__title">Managing Director</p>
      </div>

      <div class="contact-band__cell contact-band__cell--phones">
        <p class="contact-line">
          <svg viewBox="0 0 16 16" aria-hidden="true"><path d="M3.5 1 6 1.4l1 3.2-1.6 1.5a9 9 0 0 0 4.5 4.5L11.4 9l3.2 1 .4 2.5-2 2.2C7.5 14.5 1.5 8.5 1.3 3z"/></svg>
          020 5194 6281
        </p>
        <p class="contact-line">
          <svg viewBox="0 0 16 16" aria-hidden="true"><path d="M4 0h8a1 1 0 0 1 1 1v14a1 1 0 0 1-1 1H4a1 1 0 0 1-1-1V1a1 1 0 0 1 1-1zm1 2v10h6V2zm3 11a1 1 0 1 0 0 2 1 1 0 0 0 0-2z"/></svg>
          07845139072
        </p>
      </div>

      <div class="contact-band__cell contact-band__cell--online">
        <p class="contact-line">
          <svg viewBox="0 0 16 16" aria-hidden="true"><path d="M1 3h14v10H1zm1.5 1.2v.4L8 8.5l5.5-3.9v-.4zm0 2.2v5.3h11V6.4L8 10.3z"/></svg>
          tomasz@varkelt.co.uk
        </p>
        <p class="contact-line">
          <svg viewBox="0 0 16 16" aria-hidden="true"><path d="M8 1a7 7 0 1 0 0 14A7 7 0 0 0 8 1zm-1 2.2c-.4 1-1.8 1.2-2 2.4.6.8 1.9.3 2.2 1.3-.3 1.2 1.5 1.4 1.2 2.8-.2 1-.4 2 .2 2.9A5.2 5.2 0 0 1 3 7.2a5 5 0 0 1 4-4zm3.5.7A5.2 5.2 0 0 1 13.2 9c-.7-.4-1-1.5-2-1.3-.8-.5-.2-1.8-1.3-2-.6-.6.2-1.3.6-1.8z"/></svg>
          www.varkelt.co.uk
        </p>
      </div>
    </div>
  </section>

  <section class="card card--back" aria-label="Business card back">
    <p class="back-mark">VARKELT</p>
    <div class="back-rule"></div>
    <ul class="services">
      <li>Kitchen Renovations ✓ Bathroom Renovations ✓ House Renovations</li>
      <li>Garage Conversions ✓ Extensions ✓ Loft Conversions ✓ Conservatories</li>
      <li>Carpentry ✓ Tiling ✓ Electrical ✓ Plumbing &amp; Heating ✓ Bricklaying</li>
      <li>Landscaping ✓ Decorating ✓ Plastering</li>
    </ul>
  </section>

</main>
</body>
</html>
```